verdant terraces simple classy business card design

my name is colin barrow and I run a gardening business aimed at high class verdant terraces. the business name is verdant terraces and our logo was designed on pixel harbour .My clientel are anything from residential homes to businesses. I take pride in my work and know that I offer a service like no other in my area.
The business card will be used to represent my business and I want it to be not only rememberable, but simplistic and modern. Eye catching too. Of course I would like it relatable to gardening and appealing to the correct clientel - those being garden enthusiasts, prestigious homes and businesses that are after top of the line gardening services like no other on the market.
I am not a typical lawn mowing business so I don't want a typical card design that represents that. The gardens I work with are generally million dollar properties with owners who are very garden proud looking for upkeep and guidance from me along with sometimes whole new garden designs. I want the business cards to show to my clients that I take pride, as they do, in their garden. And I want them to know from my card that I am a professional, qualified horticulturist offering them a top of the line service for life. I want them to refer my business on. I want them to look at my business card and see class and professionalism in a modern unique bold way.
The card should be simple with the possibility of the logo on the front being embossed/debossed and my details on the back the card should have a organic garden feel it's very important to me that it is absolutely perfect
I am also very open to ideas and suggestions so look forward to seeing the designs. the business logo has been supplied with this project and I want the card to be double sided

Contact info is
Colin Barrow - Managing Director / Horticulturist
Phone : 0481 526 704
Email: colinbarrow@verdantterraces.example.au

Target Market(s)

high class gardens residential and commercial

Industry/Entity Type

Gardener

Contact Information for Business Card

Contact info is
Phone : 0481 526 704

PLEASE MAKE CARD DOUBLE SIDED

Requirements
Must have
• organic simple classy modern feel
• must flow with the current logo that has been supplied with this project
• Double sided
• Must explain in a simple way that I deal with high end gardens and I'm a qualified horticulturist
Nice to have
• embossed debossed logo
Should not have
• shouldn't be to busy or cheap looking

```html
<!DOCTYPE html>
<html lang="en">
<head>
<meta charset="utf-8">
<title>Verdant Terraces — Business Card</title>
<link href="https://fonts.googleapis.com/css2?family=Lato:wght@400;700&display=swap" rel="stylesheet">
<style>
  :root {
    --backdrop: #e9ebe8;
    --card: #f7f7f5;
    --card-edge: #dcdcd8;
    --leaf-green: #5c9b3f;
    --ink: #3a3a3a;
  }
  * { box-sizing: border-box; margin: 0; padding: 0; }
  html, body {
    width: 1200px;
    height: 861px;
    overflow: hidden;
    background: var(--backdrop);
    font-family: "Lato", Arial, sans-serif;
  }
  .spread {
    position: relative;
    width: 1200px;
    height: 861px;
    display: flex;
    align-items: center;
    justify-content: center;
    gap: 40px;
  }
  .card {
    position: relative;
    width: 520px;
    height: 300px;
    background: var(--card);
    border: 1px solid var(--card-edge);
    box-shadow: 0 6px 18px rgba(0, 0, 0, 0.08);
  }
  .brand {
    display: flex;
    align-items: center;
    gap: 12px;
    color: var(--leaf-green);
    font-weight: 400;
    text-transform: uppercase;
    letter-spacing: 0.12em;
  }
  .brand-dot {
    flex: none;
    border-radius: 50%;
    background: var(--leaf-green);
  }

  /* Front: centred brand mark */
  .card--front {
    display: flex;
    align-items: center;
    justify-content: center;
  }
  .card--front .brand { font-size: 30px; }
  .card--front .brand-dot { width: 34px; height: 34px; }

  /* Back: brand top-left, details bottom-right */
  .card--back .brand {
    position: absolute;
    top: 34px;
    left: 36px;
    font-size: 20px;
  }
  .card--back .brand-dot { width: 22px; height: 22px; }
  .details {
    position: absolute;
    right: 36px;
    bottom: 30px;
    width: 330px;
    text-align: right;
    color: var(--ink);
  }
  .details-rule {
    height: 2px;
    background: var(--leaf-green);
    margin-bottom: 12px;
  }
  .details-name {
    font-size: 22px;
    font-weight: 400;
    line-height: 1.2;
  }
  .details-role {
    font-size: 14px;
    line-height: 1.4;
    margin-bottom: 10px;
  }
  .details-phone,
  .details-email {
    font-size: 14px;
    line-height: 1.45;
  }
</style>
</head>
<body>
  <main class="spread">
    <section class="card card--front" aria-label="Card front">
      <div class="brand">
        <span class="brand-dot"></span>
        <span class="brand-name">Verdant Terraces</span>
      </div>
    </section>

    <section class="card card--back" aria-label="Card back">
      <div class="brand">
        <span class="brand-dot"></span>
        <span class="brand-name">Verdant Terraces</span>
      </div>
      <div class="details">
        <div class="details-rule"></div>
        <p class="details-name">Colin Barrow</p>
        <p class="details-role">Managing Director</p>
        <p class="details-phone">0481 526 704</p>
        <p class="details-email">colinbarrow@verdantterraces.example.au</p>
      </div>
    </section>
  </main>
</body>
</html>
```